Custom unique Stationary design for Logistics company

We need a custom, unique , elegant and luxurious full stationary design using our new logo, following these guidelines:
1- Business card: double sided, both sides uses the navy blue as the background main color (same as the code of the navy blue used in our logo).
2- envelope and folder: also use the same navy blue as the main background color.
3- book cover( notepad cover) : same thing with the navy blue
4- letterhead: feel free to use the combination of the colors in our logo.
5- rest of the items are up to your creativity

Target Market(s)

corporates and other businesses

Industry/Entity Type

Logistics and heavy machines contractors

Requirements
Must have
• Letterhead, business card, envelope, notepad cover, paper, file
Nice to have
• navy blue to be main background color for business card, envelope, notepad cover

```html
<!DOCTYPE html>
<html lang="en">
<head>
<meta charset="utf-8">
<title>Northline Freight – Business Card</title>
<link href="https://fonts.googleapis.com/css2?family=Open+Sans:wght@400;600;700;800&display=swap" rel="stylesheet">
<style>
  :root {
    --navy: #0f4e78;
    --orange: #f15a22;
    --white: #ffffff;
    --stage: #e6e7e9;
    --muted: #dbe6ee;
  }
  * { margin: 0; padding: 0; box-sizing: border-box; }
  html, body {
    width: 1200px; height: 800px; overflow: hidden;
    background: var(--stage);
    font-family: "Open Sans", Arial, sans-serif;
  }
  .sheet {
    width: 1200px; height: 800px;
    display: flex; align-items: center; justify-content: center; gap: 40px;
  }
  .card {
    position: relative;
    width: 540px; height: 309px;
    background: var(--navy);
    overflow: hidden;
    box-shadow: 0 6px 18px rgba(0,0,0,.18);
  }
  .card-panel { position: absolute; inset: 0; }

  /* contact side */
  .contact {
    position: absolute; left: 34px; top: 38px;
    color: var(--white);
  }
  .contact-name { font-size: 18px; font-weight: 700; letter-spacing: .5px; text-transform: uppercase; }
  .contact-role { font-size: 14px; font-weight: 600; color: var(--orange); margin-bottom: 10px; }
  .contact-line { display: flex; align-items: center; gap: 9px; font-size: 14px; line-height: 23px; }
  .contact-line svg { width: 12px; height: 12px; flex: none; }

  .address {
    position: absolute; right: 300px; bottom: 34px;
    color: var(--muted); font-size: 14.5px; line-height: 22px; text-align: right; font-style: normal;
  }
  .wordmark {
    position: absolute; display: flex; align-items: center; gap: 8px;
    font-weight: 800; letter-spacing: .3px; white-space: nowrap;
  }
  .wordmark-dot { border-radius: 50%; background: var(--orange); flex: none; }
  .wordmark--back { right: 26px; top: 140px; color: var(--navy); font-size: 19px; }
  .wordmark--back .wordmark-dot { width: 11px; height: 11px; }

  /* brand side */
  .wordmark--front {
    left: 0; right: 0; top: 0; bottom: 0; justify-content: center;
    color: var(--white); font-size: 40px; gap: 12px;
  }
  .wordmark--front .wordmark-dot { width: 22px; height: 22px; }
</style>
</head>
<body>
<main class="sheet">

  <section class="card card--back" aria-label="Business card, contact side">
    <svg class="card-panel" viewBox="0 0 540 309" aria-hidden="true">
      <polygon points="318,0 540,0 540,309 262,309" fill="var(--white)"/>
      <polygon points="310,0 318,0 262,309 254,309" fill="var(--orange)"/>
    </svg>

    <div class="contact">
      <p class="contact-name">Martin Calloway</p>
      <p class="contact-role">Managing Director</p>
      <p class="contact-line">
        <svg viewBox="0 0 12 12"><path d="M2.5 1 L4.5 1 L5.3 3.6 L4 4.6 Q5 7 7.4 8 L8.4 6.7 L11 7.5 L11 9.5 Q10.5 11 9 11 Q2 10.3 1 3 Q1 1.5 2.5 1 Z" fill="var(--orange)"/></svg>
        555-014-2290
      </p>
      <p class="contact-line">
        <svg viewBox="0 0 12 12"><rect x="0.5" y="2" width="11" height="8" rx="1" fill="var(--orange)"/><path d="M1 2.6 L6 6.5 L11 2.6" stroke="var(--navy)" stroke-width="1.1" fill="none"/></svg>
        info@northlinefreight.com
      </p>
      <p class="contact-line">
        <svg viewBox="0 0 12 12"><circle cx="6" cy="6" r="5" fill="none" stroke="var(--orange)" stroke-width="1.4"/><path d="M1 6 H11 M6 1 Q3 6 6 11 Q9 6 6 1" fill="none" stroke="var(--orange)" stroke-width="1"/></svg>
        www.northlinefreight.com
      </p>
    </div>

    <address class="address">
      Northline Freight Company<br>
      48 Harbor Avenue, Suite 210<br>
      Easton, PA 18042
    </address>

    <p class="wordmark wordmark--back"><span class="wordmark-dot"></span>Northline Freight</p>
  </section>

  <section class="card card--front" aria-label="Business card, brand side">
    <p class="wordmark wordmark--front"><span class="wordmark-dot"></span>Northline Freight</p>
  </section>

</main>
</body>
</html>
```